Silvermoor Property Development Co.

We need a logo and business card design for a Hong Kong based real estate company, PLX Land. We are want the brand to reflect the owners forward thinking, creative, and trend setting projects, while also reflecting a sense of security and strength. We invest in industrial properties which we convert to co-living or co-working spaces. PLX stands for Greater Bay Area which is the region around southern China including HK, Macau, and 9 other Chinese cities...made up of approx. 68 million people. There are massive infrastructure projects including the bridge to Macau and high-speed rail to SZ and the bridge connecting SZ and Zhongshan.

Target Market(s)

Chinese and western retail investors, as well as institutional investors

Industry/Entity Type

Real Estate Development

Contact Information for Business Card

Dale Whitford
CEO
dale@plxland-example.com
M + 852 9581 4062
F + 852 3864 2217
Suite 2207, The Halvern, 41 Tremont Rd., Central, Hong Kong

Logo Text

plx land (company name) lifestyle property development (underneath)

Colors

Designer to choose colors to be used in the design.

Requirements
Must have
• Details listed above. One side should include the logo and company name...plx land in modern, hip styling with "lifestyle property development"
Nice to have
• Could be a Black card, with metallic purple "plx" and white "land"...but open great design ideas
Should not have
• boring and traditional layout

```html
<!DOCTYPE html>
<html lang="en">
<head>
<meta charset="utf-8">
<title>PLX Land – Business Card</title>
<link href="https://fonts.googleapis.com/css2?family=Oswald:wght@500&family=Roboto:wght@400&display=swap" rel="stylesheet">
<style>
  :root {
    --backdrop: #3b3b3d;
    --backdrop-edge: #1f1f21;
    --card-purple: #6a2ba3;
    --card-purple-deep: #5a2490;
    --emboss-light: #7e42b8;
    --emboss-dark: #4e1f80;
    --silver: #e2dfea;
    --silver-soft: #cfc8dc;
  }
  * { margin: 0; padding: 0; box-sizing: border-box; }
  html, body { width: 1200px; height: 900px; overflow: hidden; }
  body {
    background: radial-gradient(ellipse at center, var(--backdrop) 0%, var(--backdrop-edge) 100%);
    position: relative;
  }
  .card {
    position: absolute;
    width: 620px;
    height: 354px;
    border-radius: 4px;
    background: radial-gradient(ellipse at 55% 45%, var(--card-purple) 0%, var(--card-purple-deep) 100%);
    box-shadow: 0 14px 30px rgba(0,0,0,0.45);
  }
  .card--front { left: 290px; top: 70px; }
  .card--back  { left: 290px; top: 476px; }

  /* Front */
  .brand {
    position: absolute;
    left: 0; right: 0; top: 140px;
    display: flex;
    justify-content: center;
    align-items: center;
    gap: 16px;
  }
  .brand__dot {
    width: 18px; height: 18px;
    border-radius: 50%;
    background: var(--silver);
  }
  .brand__name {
    font-family: "Roboto", sans-serif;
    font-weight: 400;
    font-size: 60px;
    line-height: 1;
    color: var(--silver);
  }
  .brand__tagline {
    position: absolute;
    right: 36px; bottom: 32px;
    font-family: "Roboto", sans-serif;
    font-size: 14px;
    letter-spacing: 0.3px;
    color: var(--silver-soft);
  }

  /* Back */
  .person {
    position: absolute;
    right: 340px; top: 112px;
    text-align: right;
  }
  .person__name {
    font-family: "Oswald", sans-serif;
    font-weight: 500;
    font-size: 34px;
    letter-spacing: 0.5px;
    line-height: 1.1;
    color: var(--emboss-dark);
    text-shadow: 1px 1px 0 var(--emboss-light);
    text-transform: uppercase;
  }
  .person__role {
    font-family: "Roboto", sans-serif;
    font-size: 14px;
    color: var(--emboss-dark);
    text-shadow: 1px 1px 0 var(--emboss-light);
  }
  .divider {
    position: absolute;
    left: 300px; top: 118px;
    width: 1px; height: 78px;
    background: var(--emboss-dark);
    box-shadow: 1px 0 0 var(--emboss-light);
  }
  .contacts {
    position: absolute;
    left: 322px; top: 122px;
    list-style: none;
  }
  .contacts__item {
    display: flex;
    align-items: center;
    gap: 9px;
    font-family: "Roboto", sans-serif;
    font-size: 17px;
    line-height: 24px;
    color: var(--silver);
  }
  .contacts__icon { width: 12px; height: 12px; fill: var(--silver); flex: none; }
  .address {
    position: absolute;
    left: 40px; bottom: 40px;
    font-family: "Roboto", sans-serif;
    font-size: 15px;
    color: var(--emboss-dark);
    text-shadow: 1px 1px 0 var(--emboss-light);
  }
</style>
</head>
<body>
  <section class="card card--front" aria-label="Card front">
    <div class="brand">
      <span class="brand__dot" aria-hidden="true"></span>
      <span class="brand__name">PLX Land</span>
    </div>
    <div class="brand__tagline">Lifestyle property development</div>
  </section>

  <section class="card card--back" aria-label="Card back">
    <div class="person">
      <div class="person__name">Dale Whitford</div>
      <div class="person__role">CEO</div>
    </div>
    <div class="divider"></div>
    <ul class="contacts">
      <li class="contacts__item">
        <svg class="contacts__icon" viewBox="0 0 12 12" aria-hidden="true"><path d="M2.5 0.5l2 2.3-1.1 1.3c.7 1.6 2 2.9 3.6 3.6l1.3-1.1 2.3 2-1.3 2C5 10.4 1.6 7 0.5 2.5z"/></svg>
        + 852 9581 4062
      </li>
      <li class="contacts__item">
        <svg class="contacts__icon" viewBox="0 0 12 12" aria-hidden="true"><rect x="3" y="0.5" width="6" height="3"/><rect x="0.5" y="4" width="11" height="5" rx="1"/><rect x="3" y="8" width="6" height="3.5"/></svg>
        + 852 3864 2217
      </li>
      <li class="contacts__item">
        <svg class="contacts__icon" viewBox="0 0 12 12" aria-hidden="true"><path d="M0.5 2h11v8h-11z M1.5 3l4.5 3.5 4.5-3.5" fill="none" stroke="#e2dfea" stroke-width="1"/></svg>
        dale@plxland-example.com
      </li>
    </ul>
    <div class="address">Suite 2207, The Halvern, 41 Tremont Rd., Central, Hong Kong</div>
  </section>
</body>
</html>
```